Business Card Design For Office Furniture Clearance Company

Kestrel Office Clearance - our company name pretty much explains what we do, we clear offices for high end clients, mainly plc's and large international companies.

We require a nice looking business card that displays professionalism but without being too serious.

It would be nice to see just a little more than a conventional boring business card, make sure you add some flare.

Industry/Entity Type

Office Furniture

Contact Information for Business Card

CARD 1

Mark Holloway
Director
mark@kestrelofficeclearance.co.uk
m: 07700 153928

t: 01632 960418
www.kestrelofficeclearance.co.uk

Kestrel Office Clearance
Unit K4 B
2-8 Fenwick Lane
Ashbury
Norbridge
ZZ9 4QT

no-cost office clearances… it really is that simple.

CARD 2

Peter Radford
Director
peter@kestrelofficeclearance.co.uk
m: 07700 382615

t: 01632 960418

Kestrel Office Clearance
Unit K4 B
2-8 Fenwick Lane
Ashbury
Norbridge
ZZ9 4QT

Font styles to use
Sans Serif

Requirements
Must have
• A white background - as we have a blue logo.
Nice to have
• Nice use of the logo - play around with this and dissect it.

```html
<!DOCTYPE html>
<html lang="en">
<head>
<meta charset="utf-8">
<title>Kestrel Office Clearance – Business Card</title>
<link rel="stylesheet" href="https://fonts.googleapis.com/css2?family=Open+Sans:wght@400;600&display=swap">
<style>
  :root {
    --brand-blue: #0b64a0;
    --brand-blue-deep: #08548a;
    --brand-blue-light: #2a86c8;
    --ink: #1b1b1b;
    --paper: #ffffff;
    --backdrop: #e6e8eb;
  }
  * { box-sizing: border-box; margin: 0; padding: 0; }
  html, body {
    width: 1200px; height: 864px; overflow: hidden;
    background: var(--backdrop);
    font-family: "Open Sans", sans-serif;
  }
  .stage { position: relative; width: 1200px; height: 864px; }

  .card {
    position: absolute;
    width: 560px; height: 340px;
    box-shadow: 0 6px 18px rgba(0,0,0,.18);
    overflow: hidden;
  }

  /* Card back */
  .card-back {
    left: 150px; top: 60px;
    background: radial-gradient(circle at 50% 38%, var(--brand-blue-light) 0%, var(--brand-blue) 55%, var(--brand-blue-deep) 100%);
  }
  .card-back .brand-disc {
    position: absolute; left: 50%; top: 52px;
    width: 120px; height: 120px; margin-left: -60px;
    border-radius: 50%; background: var(--paper);
  }
  .card-back .brand-name {
    position: absolute; left: 0; right: 0; top: 188px;
    text-align: center; color: var(--paper);
    font-weight: 600; font-size: 20px; letter-spacing: .3px;
  }
  .card-back .tagline-band {
    position: absolute; left: 0; right: 0; top: 248px; height: 42px;
    background: var(--paper);
    display: flex; align-items: center; padding-left: 30px;
  }
  .card-back .tagline {
    color: var(--brand-blue); font-weight: 600; font-size: 19px; white-space: nowrap;
  }

  /* Card front */
  .card-front {
    left: 490px; top: 460px;
    background: var(--paper);
  }
  .card-front .brand-mark {
    position: absolute; left: 34px; top: 34px;
    display: flex; align-items: center; gap: 12px;
  }
  .card-front .brand-disc {
    width: 96px; height: 96px; border-radius: 50%;
    background: var(--brand-blue-light);
  }
  .card-front .brand-mark .brand-name {
    color: var(--brand-blue); font-weight: 600; font-size: 15px;
    line-height: 1.25; width: 110px;
  }
  .contact-person {
    position: absolute; right: 30px; top: 36px; text-align: right;
  }
  .contact-person .person-name {
    color: var(--brand-blue); font-weight: 600; font-size: 19px; line-height: 1.2;
  }
  .contact-person .person-role {
    color: var(--ink); font-size: 13px;
  }
  .contact-list {
    position: absolute; right: 30px; top: 178px;
    list-style: none; text-align: right;
  }
  .contact-list li {
    display: flex; justify-content: flex-end; align-items: center; gap: 8px;
    color: var(--ink); font-size: 14px; line-height: 22px;
  }
  .contact-list svg { width: 13px; height: 13px; fill: var(--brand-blue); flex: none; }
  .company-block {
    position: absolute; right: 30px; bottom: 26px; text-align: right;
  }
  .company-block .company-name {
    color: var(--brand-blue); font-weight: 600; font-size: 18px; line-height: 1.3;
  }
  .company-block .address {
    color: var(--ink); font-size: 14px; white-space: nowrap;
  }
</style>
</head>
<body>
<main class="stage">

  <section class="card card-back" aria-label="Business card, back">
    <div class="brand-disc"></div>
    <div class="brand-name">Kestrel Office Clearance</div>
    <div class="tagline-band">
      <p class="tagline">no-cost office clearances… it really is that simple</p>
    </div>
  </section>

  <section class="card card-front" aria-label="Business card, front">
    <div class="brand-mark">
      <div class="brand-disc"></div>
      <div class="brand-name">Kestrel Office Clearance</div>
    </div>

    <div class="contact-person">
      <div class="person-name">Mark Holloway</div>
      <div class="person-role">Director</div>
    </div>

    <ul class="contact-list">
      <li>07700 153928
        <svg viewBox="0 0 16 16" aria-hidden="true"><path d="M4 0h8a1.5 1.5 0 0 1 1.5 1.5v13A1.5 1.5 0 0 1 12 16H4a1.5 1.5 0 0 1-1.5-1.5v-13A1.5 1.5 0 0 1 4 0zm.5 2v10h7V2zM8 13a1 1 0 1 0 0 2 1 1 0 0 0 0-2z"/></svg>
      </li>
      <li>01632 960418
        <svg viewBox="0 0 16 16" aria-hidden="true"><path d="M3.6 1.2 5.8 3.4c.4.4.4 1 0 1.4L4.6 6c.9 1.9 2.5 3.5 4.4 4.4l1.2-1.2c.4-.4 1-.4 1.4 0l2.2 2.2c.4.4.4 1 0 1.4l-1.3 1.3c-.6.6-1.6.8-2.4.4C6.6 13 3 9.4 1.5 5.9c-.4-.8-.2-1.8.4-2.4z"/></svg>
      </li>
      <li>mark@kestrelofficeclearance.co.uk
        <svg viewBox="0 0 16 16" aria-hidden="true"><path d="M1 3h14v10H1zm1.5 1.3v.2L8 8.6l5.5-4.1v-.2zm0 2.1v5.3h11V6.4L8 10.5z"/></svg>
      </li>
      <li>www.kestrelofficeclearance.co.uk
        <svg viewBox="0 0 16 16" aria-hidden="true"><path d="M8 0a8 8 0 1 0 0 16A8 8 0 0 0 8 0zm0 1.6c.9 0 2 1.9 2.3 5.6H5.7C6 3.5 7.1 1.6 8 1.6zM5.7 8.8h4.6C10 12.5 8.9 14.4 8 14.4S6 12.5 5.7 8.8zM1.7 7.2A6.4 6.4 0 0 1 5 2.1c-.5 1.2-.8 3-.9 5.1zm0 1.6h2.4c.1 2.1.4 3.9.9 5.1a6.4 6.4 0 0 1-3.3-5.1zm12.6 0a6.4 6.4 0 0 1-3.3 5.1c.5-1.2.8-3 .9-5.1zm0-1.6h-2.4c-.1-2.1-.4-3.9-.9-5.1a6.4 6.4 0 0 1 3.3 5.1z"/></svg>
      </li>
    </ul>

    <div class="company-block">
      <div class="company-name">Kestrel Office Clearance</div>
      <div class="address">Unit K4 B, 2-8 Fenwick Lane Ashbury, Norbridge&nbsp; ZZ9 4QT</div>
    </div>
  </section>

</main>
</body>
</html>
```